Business Card Design

New business card design

Target Market(s)

Residential & Commercial Property Managers

Industry/Entity Type

Plumbing Services

Contact Information for Business Card

Name - Rowan Keddle, title - Director, Phone Number - 0431 286 517, email - rowan@tbk-plumbing.com.au, Company ABN - 73 215 904 386,

Font styles to use
Sans Serif

Colors
0054AA
0677BA
7BADD7
CADEEF
E8F1F8

```html
<!DOCTYPE html>
<html lang="en">
<head>
<meta charset="utf-8">
<title>TBK Plumbing – Business Card</title>
<link rel="stylesheet" href="https://fonts.googleapis.com/css2?family=Poppins:wght@300;400;600&display=swap">
<style>
  :root {
    --backdrop: #202124;
    --card-navy: #1b2028;
    --card-navy-deep: #15191f;
    --brand-blue: #1fa3df;
    --brand-blue-deep: #0677ba;
    --brand-blue-mid: #7badd7;
    --brand-blue-pale: #cadeef;
    --brand-blue-mist: #e8f1f8;
    --surname-taupe: #8a7f72;
    --text-light: #d9dde2;
    --text-white: #ffffff;
  }
  * { box-sizing: border-box; margin: 0; padding: 0; }
  html, body {
    width: 1200px; height: 780px; overflow: hidden;
    background: var(--backdrop);
    font-family: "Poppins", Arial, sans-serif;
  }
  .canvas {
    width: 1200px; height: 780px;
    display: flex; align-items: center; justify-content: center; gap: 40px;
  }
  .card {
    width: 525px; height: 300px; position: relative; overflow: hidden;
    box-shadow: 0 14px 40px rgba(0,0,0,.55);
  }
  /* Front */
  .card-front {
    background: var(--card-navy);
    color: var(--text-light);
  }
  .card-front .light-band {
    position: absolute; left: -40px; right: -40px; top: 88px; height: 120px;
    background: linear-gradient(180deg, rgba(0,0,0,0) 0%, rgba(0,0,0,.22) 45%, rgba(255,255,255,.03) 55%, rgba(0,0,0,0) 100%);
  }
  .brand {
    position: absolute; top: 38px; left: 0; right: 0;
    display: flex; align-items: center; justify-content: center; gap: 12px;
  }
  .brand-dot {
    width: 12px; height: 12px; border-radius: 50%; background: var(--brand-blue);
  }
  .brand-name {
    font-weight: 300; font-size: 34px; letter-spacing: 1px; color: var(--text-white);
  }
  .identity {
    position: absolute; top: 108px; left: 0; right: 0; text-align: center;
  }
  .person-name { font-size: 26px; line-height: 1.1; }
  .person-name .given { font-weight: 600; color: var(--brand-blue); }
  .person-name .family { font-weight: 300; color: var(--surname-taupe); }
  .person-title { font-size: 12px; color: var(--text-white); margin-top: 3px; letter-spacing: .5px; }
  .abn { font-size: 12px; color: var(--brand-blue); margin-top: 10px; font-weight: 300; }
  .contact-list {
    position: absolute; top: 204px; left: 150px;
    list-style: none; display: grid; gap: 6px;
  }
  .contact-item {
    display: flex; align-items: center; gap: 12px;
    font-size: 12px; font-weight: 300; color: var(--text-light);
  }
  .contact-icon { width: 18px; height: 18px; flex: none; }
  /* Back */
  .card-back { background: var(--brand-blue); }
  .drop-pattern {
    position: absolute; inset: 0;
    background: linear-gradient(135deg, var(--brand-blue-deep) 0%, var(--brand-blue) 50%, var(--brand-blue-mid) 100%);
  }
</style>
</head>
<body>
<main class="canvas">
  <section class="card card-front" aria-label="Business card front">
    <div class="light-band"></div>
    <div class="brand">
      <span class="brand-dot"></span>
      <span class="brand-name">TBK Plumbing</span>
    </div>
    <div class="identity">
      <p class="person-name"><span class="given">Rowan</span> <span class="family">Keddle</span></p>
      <p class="person-title">Director</p>
      <p class="abn">ABN - 73 215 904 386</p>
    </div>
    <ul class="contact-list">
      <li class="contact-item">
        <svg class="contact-icon" viewBox="0 0 18 18" aria-hidden="true">
          <rect x="3" y="3" width="12" height="12" rx="3" transform="rotate(45 9 9)" fill="var(--brand-blue)"/>
          <path d="M6.6 5.6l1.2 1.2-.7 1a4.5 4.5 0 0 0 3.1 3.1l1-.7 1.2 1.2-.9 1.1C8.7 12.4 5.6 9.3 5.5 6.5z" fill="#fff"/>
        </svg>
        <span>0431 286 517</span>
      </li>
      <li class="contact-item">
        <svg class="contact-icon" viewBox="0 0 18 18" aria-hidden="true">
          <rect x="3" y="3" width="12" height="12" rx="3" transform="rotate(45 9 9)" fill="var(--brand-blue)"/>
          <rect x="5.5" y="6.5" width="7" height="5" rx=".6" fill="none" stroke="#fff" stroke-width="1"/>
          <path d="M5.6 6.8L9 9.4l3.4-2.6" fill="none" stroke="#fff" stroke-width="1"/>
        </svg>
        <span>rowan@tbk-plumbing.com.au</span>
      </li>
      <li class="contact-item">
        <svg class="contact-icon" viewBox="0 0 18 18" aria-hidden="true">
          <rect x="3" y="3" width="12" height="12" rx="3" transform="rotate(45 9 9)" fill="var(--brand-blue)"/>
          <circle cx="9" cy="9" r="3.6" fill="none" stroke="#fff" stroke-width="1"/>
          <path d="M5.4 9h7.2M9 5.4c-1.6 1.8-1.6 5.4 0 7.2M9 5.4c1.6 1.8 1.6 5.4 0 7.2" fill="none" stroke="#fff" stroke-width=".8"/>
        </svg>
        <span>www.tbk-plumbing.com.au</span>
      </li>
    </ul>
  </section>
  <section class="card card-back" aria-label="Business card back">
    <div class="drop-pattern" role="img" aria-label="Repeating pattern of water droplets in blue tones"></div>
  </section>
</main>
</body>
</html>
```